Brantor Works Business Card

Modern and Professional Business Card for a Med size construction/development company.

See the samples below for the design I like … but I need ideas for incorporating the red company logo while still keeping the clean look of the card samples that are attached.

Logo and tag line on the back … info on the front.

Tagline: Solid Work Begins from the Base Up

Target Market(s)

Med-Large General Contractors

Contact Information for Business Card

Brantor Works Limited
42 Fenwick Avenue
Mt. Pearl, NL
A1N 4R9

t: 709-555-0147
f: 709-555-0182
w: www.brantorworks-example.com

Font styles to use
Sans Serif

Colors
fbee3e

Requirements
Must have
• I like the black and yellow designs of the attached samples …. but I'm not sure how to incorporate the red Brantor Works logo into that design??
Nice to have
• Construction safety strips

```html
<!DOCTYPE html>
<html lang="en">
<head>
<meta charset="utf-8">
<title>Brantor Works Business Card</title>
<link rel="stylesheet" href="https://fonts.googleapis.com/css2?family=Lato:wght@400;700;900&display=swap">
<style>
  :root {
    --backdrop: #2b2b2d;
    --card: #0b0b0c;
    --brand-red: #e5232b;
    --ink-white: #f2f2f2;
    --card-shadow: rgba(0, 0, 0, 0.55);
  }
  * { box-sizing: border-box; margin: 0; padding: 0; }
  html, body {
    width: 1200px;
    height: 970px;
    overflow: hidden;
    background: var(--backdrop);
    font-family: "Lato", Arial, sans-serif;
  }
  .sheet {
    position: relative;
    width: 1200px;
    height: 970px;
  }
  .card {
    position: absolute;
    left: 220px;
    width: 760px;
    height: 434px;
    background: var(--card);
    box-shadow: 0 14px 30px var(--card-shadow);
    color: var(--ink-white);
  }
  .card--front { top: 38px; }
  .card--back { top: 498px; }

  /* Front: contact side */
  .brand-mark {
    position: absolute;
    left: 54px;
    top: 58px;
    color: var(--brand-red);
    font-weight: 900;
    font-size: 40px;
    line-height: 1.05;
    letter-spacing: 0.5px;
    text-transform: uppercase;
  }
  .contact {
    position: absolute;
    left: 54px;
    top: 196px;
  }
  .contact__company {
    color: var(--brand-red);
    font-size: 19px;
    margin-bottom: 4px;
  }
  .contact__address {
    font-size: 19px;
    line-height: 1.3;
    margin-bottom: 26px;
  }
  .contact__list { list-style: none; }
  .contact__item {
    display: flex;
    align-items: center;
    gap: 14px;
    font-size: 19px;
    line-height: 1.5;
  }
  .contact__icon {
    width: 18px;
    height: 18px;
    flex: none;
    fill: var(--brand-red);
  }
  .contact__icon--line {
    fill: none;
    stroke: var(--brand-red);
    stroke-width: 1.6;
  }
  .person {
    position: absolute;
    right: 58px;
    top: 128px;
    text-align: right;
  }
  .person__name {
    color: var(--brand-red);
    font-weight: 700;
    font-size: 32px;
    line-height: 1.1;
  }
  .person__role {
    font-size: 19px;
    margin-top: 4px;
  }

  /* Back: logo and tagline */
  .back-brand {
    position: absolute;
    left: 0;
    right: 0;
    top: 128px;
    text-align: center;
    color: var(--brand-red);
    font-weight: 900;
    font-size: 62px;
    line-height: 1.05;
    letter-spacing: 1px;
    text-transform: uppercase;
  }
  .tagline {
    position: absolute;
    left: 0;
    right: 0;
    top: 330px;
    text-align: center;
    font-size: 21px;
    letter-spacing: 1.5px;
    text-transform: uppercase;
  }
</style>
</head>
<body>
<main class="sheet">
  <section class="card card--front" aria-label="Business card front">
    <div class="brand-mark">Brantor Works<br>Limited</div>

    <div class="contact">
      <p class="contact__company">Brantor Works Limited</p>
      <p class="contact__address">42 Fenwick Avenue Mt.<br>Hollis, NL A1X 2K5</p>
      <ul class="contact__list">
        <li class="contact__item">
          <svg class="contact__icon" viewBox="0 0 24 24" aria-hidden="true">
            <path d="M3 8c0-2 2-4 9-4s9 2 9 4v2h-5V8H8v2H3z"/>
            <path d="M6 11h12l2 9H4z"/>
          </svg>
          <span>709-555-0147</span>
        </li>
        <li class="contact__item">
          <svg class="contact__icon" viewBox="0 0 24 24" aria-hidden="true">
            <rect x="7" y="3" width="10" height="6"/>
            <rect x="3" y="10" width="18" height="8" rx="1"/>
            <rect x="7" y="15" width="10" height="6"/>
          </svg>
          <span>709-555-0182</span>
        </li>
        <li class="contact__item">
          <svg class="contact__icon contact__icon--line" viewBox="0 0 24 24" aria-hidden="true">
            <circle cx="12" cy="12" r="9"/>
            <ellipse cx="12" cy="12" rx="4" ry="9"/>
            <path d="M3 12h18M5 7h14M5 17h14"/>
          </svg>
          <span>www.brantorworks-example.com</span>
        </li>
      </ul>
    </div>

    <div class="person">
      <p class="person__name">Daniel Hartley</p>
      <p class="person__role">Founder &amp; CEO</p>
    </div>
  </section>

  <section class="card card--back" aria-label="Business card back">
    <div class="back-brand">Brantor Works<br>Limited</div>
    <p class="tagline">Solid Work Begins from the Base Up</p>
  </section>
</main>
</body>
</html>
```